Quote Cards With KB May 2025 for Instagram

I would like to put these quotes over one of the pictures attached; Instagram (new size: 4:5 (1080 x 1350 pixels) One Quote per picture, and I want the quote to be bold or easy to read as well. I provided a few reference graphics that I really like as examples below. In very small letters at the bottom add @KBHarlowOnline

All of the pictures are attached; you can pick any photo and add one quote to it; but no stock photography

```html
<!DOCTYPE html>
<html lang="en">
<head>
<meta charset="utf-8">
<title>Quote Cards With KB – May 2025</title>
<link href="https://fonts.googleapis.com/css2?family=League+Gothic&family=Roboto+Condensed:wght@300;400;500;600&family=Poppins:wght@500;600&display=swap" rel="stylesheet">
<style>
  :root {
    --page: #f0f0f0;
    --ink-light: #ffffff;
    --ink-dark: #1e1e1e;
    --magenta: rgba(165, 30, 145, 0.92);
    --charcoal: rgba(48, 44, 42, 0.9);
    --slate: rgba(72, 72, 72, 0.9);
    --umber: rgba(78, 60, 46, 0.9);
    --smoke: rgba(88, 88, 88, 0.88);
    --mist: rgba(236, 236, 236, 0.82);
    --mauve: rgba(165, 95, 112, 0.9);
    --plum: rgba(36, 26, 36, 0.9);
    --steel: rgba(125, 138, 144, 0.9);
    --graphite: rgba(90, 90, 94, 0.9);
    --tag-pink: #e23c8f;
    --tag-black: #141414;
    --tag-grey: #6a6a6a;
  }
  * { margin: 0; padding: 0; box-sizing: border-box; }
  html, body { width: 1200px; height: 3217px; overflow: hidden; background: var(--page); }
  .sheet { position: relative; width: 1200px; height: 3217px; }

  .card { position: absolute; width: 461px; height: 576px; overflow: hidden; }
  .card__photo { position: absolute; inset: 0; }
  .card__panel {
    position: absolute; top: 22px; bottom: 22px;
    padding: 20px 8px 18px 16px; color: var(--ink-light);
    display: flex; flex-direction: column; white-space: nowrap;
  }
  .card__panel--dark { color: var(--ink-dark); }

  .headline { font-family: "League Gothic", "Oswald", sans-serif; font-weight: 400; letter-spacing: 0; }
  .body { font-family: "Roboto Condensed", "Arial Narrow", sans-serif; font-weight: 500; }
  .body--light { font-weight: 400; }
  .keyword { font-family: "Roboto Condensed", "Arial Narrow", sans-serif; font-weight: 500; }
  .cta { font-family: "Poppins", sans-serif; font-weight: 600; margin-top: auto; }

  .handle {
    position: absolute; bottom: 8px; width: 162px; height: 18px;
    font-family: "Poppins", sans-serif; font-weight: 500; font-size: 13px;
    color: var(--ink-light); text-align: center; line-height: 18px;
  }
  .handle--right { right: 0; }
  .handle--left { left: 0; width: 190px; }
  .handle--pink { background: var(--tag-pink); }
  .handle--black { background: var(--tag-black); }
  .handle--grey { background: var(--tag-grey); }
</style>
</head>
<body>
<main class="sheet">

  <!-- Row 1 -->
  <article class="card" style="left:120px; top:81px;">
    <div class="card__photo" role="img" aria-label="Photo of KB in a pink gown on a purple stage set" style="background:linear-gradient(120deg,#6d1f8a,#c72a9e 55%,#3a1560);"></div>
    <div class="card__panel" style="background:var(--magenta); left:19px; width:242px; padding-top:14px;">
      <h2 class="headline" style="font-size:68px; line-height:67px;">Tired.<br>Moody.<br>Stubborn<br>Belly Fat.</h2>
      <p class="body" style="font-size:34px; line-height:45px; margin-top:20px;">Your hormones<br>are screaming<br>for help!</p>
      <p class="cta" style="font-size:24px;">Let’s fix that.</p>
    </div>
    <div class="handle handle--right handle--pink">@KBHarlowOnline</div>
  </article>

  <article class="card" style="left:620px; top:81px;">
    <div class="card__photo" role="img" aria-label="Photo of KB standing courtside in an arena" style="background:linear-gradient(180deg,#1c2236,#4a4a55 45%,#7a5e3a 75%,#d9a326);"></div>
    <div class="card__panel" style="background:var(--charcoal); left:15px; width:260px; padding-top:16px;">
      <h2 class="headline" style="font-size:56px; line-height:62px;">That stubborn<br>weight?<br>It’s not your<br>fault</h2>
      <p class="body" style="font-size:33px; line-height:44px; margin-top:20px;">Your hormones<br>are to blame<br>and you’re not<br>alone;</p>
      <p class="cta" style="font-size:21px;">But there is a fix.</p>
    </div>
    <div class="handle handle--right handle--black">@KBHarlowOnline</div>
  </article>

  <!-- Row 2 -->
  <article class="card" style="left:120px; top:693px;">
    <div class="card__photo" role="img" aria-label="Photo of KB in black outfit on a sunny hillside" style="background:linear-gradient(160deg,#c9dced,#e8eef3 40%,#6f7d4e 80%,#3b4a2a);"></div>
    <div class="card__panel" style="background:var(--slate); left:190px; width:260px; padding-top:18px;">
      <h2 class="headline" style="font-size:62px; line-height:63px;">Your belly<br>isn’t fat…<br>it’s hormonal.</h2>
      <p class="body" style="font-size:34px; line-height:40px; margin-top:12px;">And here’s<br>how to fix it.</p>
      <p class="body body--light" style="font-size:34px; line-height:42px;">Comment</p>
      <p class="keyword" style="font-size:38px; line-height:42px;">HORMONES</p>
      <p class="body body--light" style="font-size:34px; line-height:42px;">if nothing is<br>working.</p>
    </div>
    <div class="handle handle--left handle--black">@KBHarlowOnline</div>
  </article>

  <article class="card" style="left:620px; top:693px;">
    <div class="card__photo" role="img" aria-label="Photo of KB in sheer black outfit by a night city window" style="background:linear-gradient(150deg,#2a2a30,#5a4a3c 50%,#1e1a18);"></div>
    <div class="card__panel" style="background:var(--umber); left:190px; width:260px; padding-top:12px;">
      <h2 class="headline" style="font-size:56px; line-height:66px;">The stubborn<br><span style="font-size:86px;">belly fat</span><br>after 40?</h2>
      <p class="body" style="font-size:33px; line-height:45px; margin-top:40px;">It’s not about<br>calories;<br>it’s about your<br>hormones.</p>
      <p class="cta" style="font-size:24px;">Here is the fix!</p>
    </div>
    <div class="handle handle--left handle--black">@KBHarlowOnline</div>
  </article>

  <!-- Row 3 -->
  <article class="card" style="left:120px; top:1308px;">
    <div class="card__photo" role="img" aria-label="Photo of KB in sheer black top in a bright apartment" style="background:linear-gradient(120deg,#b9c0c8,#e5e5e5 55%,#8d8a88);"></div>
    <div class="card__panel" style="background:var(--smoke); left:9px; width:249px; top:28px; bottom:27px; padding-top:26px;">
      <h2 class="headline" style="font-size:58px; line-height:61px;">Flat tummy<br>in your 40s?</h2>
      <p class="body" style="font-size:29px; line-height:41px; margin-top:44px;">It’s still possible!<br>Comment</p>
      <p class="keyword" style="font-size:44px; line-height:52px;">BYE BELLY</p>
      <p class="body" style="font-size:29px; line-height:41px;">to get the 10<br>secrets to a<br>flatter tummy</p>
    </div>
    <div class="handle handle--right handle--pink">@KBHarlowOnline</div>
  </article>

  <article class="card" style="left:620px; top:1308px;">
    <div class="card__photo" role="img" aria-label="Photo of KB in white crop sweater pointing upward" style="background:linear-gradient(120deg,#e6e6e6,#cfcfcf 50%,#262626);"></div>
    <div class="card__panel card__panel--dark" style="background:var(--mist); left:10px; width:248px; top:28px; bottom:27px; padding-top:22px;">
      <h2 class="headline" style="font-size:58px; line-height:60px;">Bloating.<br>Muffin top.<br><span style="font-size:48px;">Puffy waistline.</span></h2>
      <p class="body" style="font-size:34px; line-height:48px; margin-top:10px;">Your body’s<br>screaming for<br>a different<br>kind of fix</p>
      <p class="cta" style="font-size:26px;">Here it is</p>
    </div>
    <div class="handle handle--right handle--pink">@KBHarlowOnline</div>
  </article>

  <!-- Row 4 -->
  <article class="card" style="left:120px; top:1930px;">
    <div class="card__photo" role="img" aria-label="Photo of KB in a pink dress beside a sunflower display" style="background:linear-gradient(120deg,#6a5a38,#c9a23a 45%,#b9a9a2);"></div>
    <div class="card__panel" style="background:var(--mauve); left:207px; width:244px; top:28px; bottom:25px; padding-top:14px;">
      <h2 class="headline" style="font-size:48px; line-height:50px;">You’re doing<br>all the “right”<br>things, but your<br>belly won’t go<br>down?</h2>
      <p class="body" style="font-size:38px; line-height:53px; margin-top:40px;">Here’s what<br>you haven’t<br>tried.</p>
    </div>
    <div class="handle handle--left handle--pink">@KBHarlowOnline</div>
  </article>

  <article class="card" style="left:620px; top:1930px;">
    <div class="card__photo" role="img" aria-label="Photo of KB holding a basketball courtside with crowd behind" style="background:linear-gradient(120deg,#1f2a4a,#3d3a44 50%,#2a5aa8);"></div>
    <div class="card__panel" style="background:var(--plum); left:205px; width:245px; top:28px; bottom:25px; padding-top:12px;">
      <h2 class="headline" style="font-size:42px; line-height:50px;">This 90-day plan<br><span style="font-size:48px;">helped women</span><br>over 40 slim down,</h2>
      <p class="body" style="font-size:38px; line-height:52px; margin-top:26px;">Get a tiny<br>waist and<br>feel sexy<br>again.</p>
      <p class="cta" style="font-size:25px;">You’re next.</p>
    </div>
    <div class="handle handle--left handle--pink">@KBHarlowOnline</div>
  </article>

  <!-- Row 5 -->
  <article class="card" style="left:120px; top:2561px;">
    <div class="card__photo" role="img" aria-label="Photo of KB smiling in black top against blue sky and hills" style="background:linear-gradient(170deg,#a9cbe8,#dfe9f1 45%,#5b6b4a 80%,#2a2a2a);"></div>
    <div class="card__panel" style="background:var(--steel); left:12px; width:248px; top:28px; bottom:25px; padding-top:16px; padding-left:14px;">
      <h2 class="headline" style="font-size:42px; line-height:44px;">This is the secret<br>women over 40<br>are using to get<br>snatched; without<br>starving.</h2>
      <p class="body" style="font-size:33px; line-height:43px; margin-top:40px;">Comment</p>
      <p class="keyword" style="font-size:54px; line-height:60px;">SKINNY</p>
      <p class="body" style="font-size:33px; line-height:43px;">to get the<br>exact plan.</p>
    </div>
    <div class="handle handle--right handle--black">@KBHarlowOnline</div>
  </article>

  <article class="card" style="left:620px; top:2561px;">
    <div class="card__photo" role="img" aria-label="Photo of KB in black leather jacket looking back over her shoulder" style="background:linear-gradient(120deg,#4a4a4e,#8a8a8e 55%,#1a1a1c);"></div>
    <div class="card__panel" style="background:var(--graphite); left:17px; width:260px; top:28px; bottom:25px; padding-top:18px;">
      <h2 class="headline" style="font-size:56px; line-height:55px;">What worked<br>in your 30s<br>won’t work<br>now.</h2>
      <p class="body" style="font-size:33px; line-height:45px; margin-top:44px;">Here’s what<br>actually does.<br>Drop 30 Pounds<br>in 3 Months.</p>
    </div>
    <div class="handle handle--right handle--grey">@KBHarlowOnline</div>
  </article>

</main>
</body>
</html>
```